business card deign

Logo needs the following on it.
1. attached logo
2. Tagline - "If it keeps a drink cold or the party going...we do it!"
3. Name- Dalton Pikes, Founder and CPO
4. Address - 412 E. Carver Avenue, Ste 2207, Tampa, FL. 33917
5. Phone - 555.318.4726

```html
<!DOCTYPE html>
<html lang="en">
<head>
<meta charset="utf-8">
<title>Hopvale Business Card</title>
<link href="https://fonts.googleapis.com/css2?family=Open+Sans:wght@400;600;700&display=swap" rel="stylesheet">
<style>
  :root {
    --stage: #232323;
    --card-dark: #111111;
    --card-light: #ffffff;
    --ink: #111111;
    --paper: #ffffff;
  }
  * { margin: 0; padding: 0; box-sizing: border-box; }
  html, body {
    width: 1200px; height: 711px; overflow: hidden;
    background: var(--stage);
    font-family: "Open Sans", Arial, sans-serif;
  }
  .stage {
    position: relative; width: 1200px; height: 711px;
    display: flex; align-items: center; justify-content: center; gap: 50px;
  }
  .card {
    position: relative; width: 525px; height: 300px;
    border-radius: 26px; overflow: hidden;
  }
  .card--front {
    background: var(--card-dark);
    display: flex; align-items: center; justify-content: center;
  }
  .brand {
    display: flex; align-items: center; gap: 14px;
    font-weight: 700; text-transform: uppercase;
  }
  .brand__mark { width: 14px; height: 14px; border-radius: 50%; }
  .brand--large { color: var(--paper); font-size: 44px; letter-spacing: 0.32em; }
  .brand--large .brand__mark { background: var(--paper); }
  .brand--small { color: var(--ink); font-size: 20px; letter-spacing: 0.3em; gap: 8px; }
  .brand--small .brand__mark { width: 8px; height: 8px; background: var(--ink); }
  .card--back { background: var(--card-light); color: var(--ink); }
  .card--back .brand { position: absolute; top: 48px; right: 34px; }
  .details { position: absolute; left: 40px; bottom: 34px; }
  .details__bar {
    position: absolute; left: -40px; top: 4px;
    width: 18px; height: 50px; background: var(--ink);
  }
  .details__name { font-size: 24px; font-weight: 700; line-height: 1.15; }
  .details__title { font-size: 14px; font-weight: 600; margin-bottom: 12px; }
  .details__tagline { font-size: 13px; line-height: 1.35; margin-bottom: 10px; }
  .contact { list-style: none; font-size: 13px; line-height: 1.35; }
  .contact__item { display: flex; align-items: flex-start; gap: 8px; }
  .contact__icon { width: 12px; height: 12px; margin-top: 3px; flex: none; }
</style>
</head>
<body>
<main class="stage">
  <section class="card card--front">
    <div class="brand brand--large"><span class="brand__mark"></span>Hopvale</div>
  </section>

  <section class="card card--back">
    <div class="brand brand--small"><span class="brand__mark"></span>Hopvale</div>
    <div class="details">
      <span class="details__bar"></span>
      <h1 class="details__name">Dalton Pikes</h1>
      <p class="details__title">Founder and CPO</p>
      <p class="details__tagline">If it keeps a drink cold or<br>the party going...we do it!</p>
      <ul class="contact">
        <li class="contact__item">
          <svg class="contact__icon" viewBox="0 0 24 24" aria-hidden="true"><path fill="currentColor" d="M6.6 10.8a15 15 0 0 0 6.6 6.6l2.2-2.2c.3-.3.7-.4 1-.2 1.1.4 2.3.6 3.6.6.6 0 1 .4 1 1V20c0 .6-.4 1-1 1C10.6 21 3 13.4 3 4c0-.6.4-1 1-1h3.5c.6 0 1 .4 1 1 0 1.3.2 2.5.6 3.6.1.3 0 .7-.2 1z"/></svg>
          <span>555.318.4726</span>
        </li>
        <li class="contact__item">
          <svg class="contact__icon" viewBox="0 0 24 24" aria-hidden="true"><path fill="currentColor" d="M12 2a7 7 0 0 0-7 7c0 5.2 7 13 7 13s7-7.8 7-13a7 7 0 0 0-7-7zm0 9.5A2.5 2.5 0 1 1 12 6.5a2.5 2.5 0 0 1 0 5z"/></svg>
          <span>412 E. Carver Avenue,<br>Ste 2207, Tampa, FL. 33917</span>
        </li>
      </ul>
    </div>
  </section>
</main>
</body>
</html>
```